Climbing Gear Company Stationary Design

We need some new stationary to standardise our business.
We require:

Business Card
A4 Letterhead
With complements slip

Our business is a Distributor and retailer of rock climbing equipment throughout Australia.
We need to the stationary (business card in particular) to reflect this.

Target Market(s)

customers, other retail outlets, overseas manufacturers.

Industry/Entity Type

Business

Requirements
Must have
• company logo
website url- www.ridgetopgearworks.com.au
email - mark@ridgetopgearworks.com
Business Address: Unit 3, 14-16 Marlowe Street, Tallowood Bay, North Coast, 2371
Phone: 0438 627 194
my Name (on Business card) - Gordon Pellimore
use of Blue colour in our logo

```html
<!DOCTYPE html>
<html lang="en">
<head>
<meta charset="utf-8">
<title>Ridgetop Gearworks – Business Card</title>
<link href="https://fonts.googleapis.com/css2?family=Open+Sans:wght@400;600;700;800&display=swap" rel="stylesheet">
<style>
  :root {
    --navy: #1f3f8a;
    --panel-blue: #22438a;
    --card-white: #ffffff;
    --backdrop: #e9e6e1;
    --ink: #1a1a1a;
    --silver-light: #d9d9d9;
    --silver-dark: #6e6e6e;
  }
  * { margin: 0; padding: 0; box-sizing: border-box; }
  html, body {
    width: 1200px; height: 483px; overflow: hidden;
    background: var(--backdrop);
    font-family: "Open Sans", Arial, sans-serif;
  }
  .stage { position: relative; width: 1200px; height: 483px; }
  .card {
    position: absolute; top: 90px;
    width: 525px; height: 300px;
    background: var(--card-white);
    overflow: hidden;
    box-shadow: 0 2px 6px rgba(0,0,0,0.25);
  }
  .card--front { left: 58px; }
  .card--back { left: 610px; }
  .card__shapes { position: absolute; inset: 0; }

  .wordmark {
    position: absolute;
    color: var(--navy);
    font-weight: 800;
    white-space: nowrap;
    letter-spacing: 0.5px;
  }
  .tagline {
    position: absolute;
    color: var(--navy);
    font-weight: 400;
    white-space: nowrap;
    letter-spacing: 2.6px;
  }
  .card--front .wordmark { left: 26px; top: 117px; font-size: 22px; }
  .card--front .tagline { left: 26px; top: 148px; font-size: 9.5px; }

  .contact {
    position: absolute; left: 327px; top: 0; height: 100%;
    color: var(--card-white);
  }
  .contact__name {
    position: absolute; top: 43px; left: 0;
    font-size: 14.5px; font-weight: 600; white-space: nowrap;
  }
  .contact__address { position: absolute; top: 114px; left: 10px; font-size: 11.5px; line-height: 20px; white-space: nowrap; }
  .contact__lines { position: absolute; top: 190px; left: 10px; font-size: 11.5px; line-height: 20.5px; white-space: nowrap; }

  .card--back .wordmark { left: 0; right: 0; text-align: center; top: 128px; font-size: 31px; }
  .card--back .tagline { left: 0; right: 0; text-align: center; top: 170px; font-size: 12px; letter-spacing: 3.4px; }
  .card--back .web {
    position: absolute; left: 0; right: 0; top: 197px;
    text-align: center; font-size: 12.5px; color: var(--ink);
  }
</style>
</head>
<body>
<main class="stage">
  <section class="card card--front">
    <svg class="card__shapes" width="525" height="300" viewBox="0 0 525 300" aria-hidden="true">
      <defs>
        <linearGradient id="silver" x1="0" y1="0" x2="0" y2="1">
          <stop offset="0" stop-color="#6e6e6e"/>
          <stop offset="0.5" stop-color="#d9d9d9"/>
          <stop offset="1" stop-color="#6e6e6e"/>
        </linearGradient>
      </defs>
      <path d="M277 0 Q385 150 262 300 L297 300 Q367 150 297 0 Z" fill="url(#silver)"/>
      <path d="M284 0 Q378 150 272 300 L297 300 Q367 150 297 0 Z" fill="#ffffff" opacity="0.6"/>
      <path d="M297 0 Q367 150 297 300 L525 300 L525 0 Z" fill="#22438a"/>
    </svg>
    <div class="wordmark">RIDGETOP GEARWORKS</div>
    <div class="tagline">THE ROCK • THE ROPE • THE ROUTE</div>
    <div class="contact">
      <h1 class="contact__name">GORDON PELLIMORE</h1>
      <p class="contact__address">Unit 3, 14-16 Marlowe Street<br>Tallowood Bay, North Coast, 2371</p>
      <p class="contact__lines">P : 0438 627 194<br>E : mark@ridgetopgearworks.com<br>W: www.ridgetopgearworks.com.</p>
    </div>
  </section>

  <section class="card card--back">
    <div class="wordmark">RIDGETOP GEARWORKS</div>
    <div class="tagline">THE ROCK • THE ROPE • THE ROUTE</div>
    <p class="web">www.ridgetopgearworks.com.</p>
  </section>
</main>
</body>
</html>
```